High-end construction company needs a business card design

We need a modern looking business card that draws people in, is memorable and looks so good people will want to sick it on their fridges.
On the first side what is needed are:
Logo
My name - Tomasz Brelwik
Title - Managing Director
Website - www.varkelt.co.uk
Email - tomasz@varkelt.co.uk
Telephone - 020 5194 6281
Mobile - 07845139072
On the back side was is needed is a list of all the services we provide:
-Kitchen Renovations
-Bathroom Renovations
-House Renovations
-Garage Conversions
-Extensions
-Loft Conversions
-Conservatories
-Carpentry
-Tiling
-Electrical
-Plumbing & Heating
-Bricklaying
-Landscaping
-Decorating
-Plastering
We would like the colours to be the same shades as on the logo with grey or black for the words.
Target Market(s)
Anyone who needs building work done
Contact Information for Business Card
This business card is for a construction company which strives to deliver excellent service and quality.
The look and feel of the card should represent this.
Requirements
Must have
- On the first side what is needed are:
Logo
My name - Tomasz Brelwik
Title - Managing Director
Website - www.varkelt.co.uk
Email - tomasz@varkelt.co.uk
Telephone - 020 5194 6281
Mobile - 07845139072
Nice to have
- Cool looking features

```html
<!DOCTYPE html>
<html lang="en">
<head>
<meta charset="utf-8">
<title>Varkelt Construction Ltd – Business Card</title>
<link rel="stylesheet" href="https://fonts.googleapis.com/css2?family=Saira:wght@400;500;700&display=swap">
<style>
  :root {
    --stage: #ececec;
    --card: #2b2b2c;
    --text: #c9c9cb;
    --text-soft: #b3b3b6;
    --green: #5cbb00;
    --rule: #8a8a8d;
    --shadow: rgba(0, 0, 0, 0.28);
  }
  * { margin: 0; padding: 0; box-sizing: border-box; }
  html, body {
    width: 1200px;
    height: 900px;
    overflow: hidden;
    background: var(--stage);
    font-family: "Saira", "Helvetica Neue", Arial, sans-serif;
  }
  .card {
    position: absolute;
    left: 280px;
    width: 640px;
    height: 365px;
    background: var(--card);
    color: var(--text);
    box-shadow: 0 10px 24px var(--shadow);
  }
  .card--front { top: 60px; }
  .card--back { top: 475px; }

  /* Front */
  .holder { position: absolute; left: 44px; top: 22px; }
  .holder__name {
    font-size: 27px;
    font-weight: 500;
    letter-spacing: 1px;
    line-height: 1.2;
  }
  .holder__title {
    font-size: 16px;
    font-weight: 500;
    letter-spacing: 2px;
    color: var(--text-soft);
  }
  .brand {
    position: absolute;
    left: 295px;
    top: 110px;
    width: 270px;
    color: var(--green);
    font-weight: 700;
    text-transform: uppercase;
  }
  .brand__name {
    font-size: 60px;
    line-height: 1;
    letter-spacing: 1px;
  }
  .brand__sub {
    margin-top: 6px;
    font-size: 16px;
    letter-spacing: 3.2px;
  }
  .contact {
    position: absolute;
    top: 283px;
    font-size: 17px;
    font-weight: 500;
    letter-spacing: 1.5px;
    line-height: 27px;
    color: var(--text-soft);
  }
  .contact--phones { left: 44px; }
  .contact--web { left: 295px; letter-spacing: 1px; }

  /* Back */
  .services__heading {
    position: absolute;
    left: 44px;
    top: 24px;
    font-size: 16px;
    font-weight: 500;
    letter-spacing: 1.5px;
  }
  .services__rule {
    position: absolute;
    height: 1px;
    background: var(--rule);
  }
  .services__rule--top { left: 44px; top: 52px; width: 110px; }
  .services__rule--right { left: 360px; top: 118px; width: 80px; }
  .services__rule--bottom { left: 44px; top: 318px; width: 420px; }
  .services__list {
    position: absolute;
    list-style: none;
    font-size: 14px;
    font-weight: 500;
    letter-spacing: 1.2px;
    line-height: 23px;
    color: var(--text);
  }
  .services__list--left { left: 44px; top: 62px; }
  .services__list--right { left: 360px; top: 128px; }
  .back-brand {
    position: absolute;
    left: 478px;
    top: 308px;
    display: flex;
    align-items: center;
    gap: 6px;
    color: var(--green);
    font-size: 14px;
    font-weight: 700;
    letter-spacing: 1px;
    text-transform: uppercase;
  }
  .back-brand__mark {
    width: 9px;
    height: 9px;
    background: var(--green);
  }
</style>
</head>
<body>

<section class="card card--front" aria-label="Business card front">
  <div class="holder">
    <p class="holder__name">Tomasz Brelwik</p>
    <p class="holder__title">Managing Director</p>
  </div>

  <div class="brand">
    <p class="brand__name">Varkelt</p>
    <p class="brand__sub">Construction Ltd</p>
  </div>

  <div class="contact contact--phones">
    <p>020 5194 6281</p>
    <p>078 4513 9072</p>
  </div>
  <div class="contact contact--web">
    <p>www.varkelt.co.uk</p>
    <p>tomasz@varkelt.co.uk</p>
  </div>
</section>

<section class="card card--back" aria-label="Business card back">
  <p class="services__heading">Services</p>
  <div class="services__rule services__rule--top"></div>
  <ul class="services__list services__list--left">
    <li>Kitchen Renovations</li>
    <li>Bathroom Renovations</li>
    <li>House Renovations</li>
    <li>Garage Conversions</li>
    <li>Extensions</li>
    <li>Loft Conversions</li>
    <li>Conservatories</li>
    <li>Carpentry</li>
  </ul>
  <div class="services__rule services__rule--right"></div>
  <ul class="services__list services__list--right">
    <li>Tiling</li>
    <li>Electrical</li>
    <li>Plumbing &amp; Heating</li>
    <li>Bricklaying</li>
    <li>Landscaping</li>
    <li>Decorating</li>
    <li>Plastering</li>
  </ul>
  <div class="services__rule services__rule--bottom"></div>
  <div class="back-brand">
    <span class="back-brand__mark"></span>
    <span>Varkelt</span>
  </div>
</section>

</body>
</html>
```